Probate (Legal) Wordpress Design with Coding for Online Company

I need a Wordpress design with coding, pictures, content to be provided by me, fully responsive, and development. This is for a 6-7 page design.

Pages Needed: Home/About/Probate/Process/FAQ/Contact Us/Blog.

The home page should be organized as followed:
-Steps in Probate: Gather; Implement; Close (each step will come with content)
-Flat-Fee Price & Savings: Content will go here with a button to contact us (phone number) or just the phone number.
-You Have Questions, We Have Answers: five questions with content. Only one question answer to show at a time when clicked on the question from the list.
-Get to Know Us: a brief description with content about what we do and who we are.

Main image slogan: Helping Californians deal with loss with DIGNITY & UNDERSTATING (you may use a better slogan if you wish).

The Contact page should not have a map since we are an online company. We service the entire state of California in every county and city.

The About page should be simple, direct, and easy on the eye. It should have a brief description of who we are and it should have no more than 6 reasons why the client should hire us.

About our online California company. We are not attorneys but legal document assistants who prepare legal documents for probate estate when someone dies with or without a will and assets need to be distributed. We have a flat-fee for Formal Probate of $999 and $699 for Informal Probate. We are an online company and offer our services to the entire state of California in every county. We do everything over the phone and email. The turn around time for us to prepare the initial legal paperwork for the client is within 3-5 business days. We can prepare, file, serve and manage a probate matter from petition to closing. We are not attorneys so our prices are very affordable compare to the attorney.

The company name for the website will be www.velmarhollow.com, The Velmar Hollow Group.

I do not have a logo yet. The colors of the website should be easy on the eye and calming. THE SITE SHOULD BE SIMPLE AND STRAIGHT TO THE POINT. EASY TO NAVIGATE.

The company phone number should be very visible and should stand out to the client. It should also be clickable and ready to dial for smartphone users.

I do not want a contact form on the homepage. THE MAIN THING IS FOR THE POTENTIAL CLIENT TO CALL OUR OFFICE TO SIGN UP.

I do like some images of family or people since we are dealing with people who just lost a loved one. Not all the images have to be of people.

The site should not look like we practice law or that people can mistake us for attorneys.

Target Market(s)

People who just lost a loved one who had property, assets, in California but died with or without a will or trust. This is for people looking to hire non-attorneys.

Coding

Coded - Design and coding required

Font styles to use
Serif

Colors

Designer to choose colors to be used in the design.

Requirements
Must have
• Refer to Project Description.
Nice to have
• The sample images provided is what I am attracted to for the homepage image.
Should not have

```html
<!DOCTYPE html>
<html lang="en">
<head>
<meta charset="utf-8">
<title>The Velmar Hollow Group</title>
<link rel="stylesheet" href="https://fonts.googleapis.com/css2?family=Noto+Serif:wght@400&family=Open+Sans:wght@400;600;700&display=swap">
<style>
:root{
  --blue:#25a6e1;
  --ink:#333;
  --muted:#555;
  --light:#f2f2f2;
  --line:#e3e3e3;
  --circle:#e2e2e2;
  --social:#dcdcdc;
  --dark:#3d4a54;
  --white:#fff;
}
*{box-sizing:border-box;margin:0;padding:0}
html,body{width:1200px;height:2281px;overflow:hidden;background:var(--white)}
body{position:relative;font-family:"Open Sans",sans-serif;color:var(--ink)}
.serif{font-family:"Noto Serif",serif;font-weight:400}
.abs{position:absolute}

.topbar{top:0;left:0;width:1200px;height:37px;background:var(--light)}
.topbar .call{left:913px;top:10px;font-size:14px;font-weight:700;display:flex;align-items:center;gap:8px}

.header{top:37px;left:0;width:1200px;height:73px;background:var(--white);box-shadow:0 2px 4px rgba(0,0,0,.08);z-index:2}
.logo{left:105px;top:19px;font-size:25px;color:var(--blue)}
.nav{top:21px;left:613px;display:flex;align-items:center;font-family:"Noto Serif",serif;font-size:13px}
.nav a{color:var(--ink);text-decoration:none;padding:0 13px;line-height:36px}
.nav a.active{background:var(--blue);color:var(--white);padding:0 18px;margin-right:6px}

.hero-scene{top:110px;left:0;width:1200px;height:428px;background:linear-gradient(180deg,#dfeaf0 0%,#c7d6df 45%,#5d9cc2 62%,#2f7fb5 100%)}
.hero-photo{top:110px;left:715px;width:485px;height:428px;background:linear-gradient(120deg,rgba(234,240,244,0),rgba(214,190,160,.75) 40%,rgba(180,150,120,.7))}
.hero-title{top:203px;left:95px;width:620px;text-align:center;font-size:31px;line-height:41px;color:#3a3a3a}
.btn{display:block;background:var(--blue);color:var(--white);font-weight:700;font-size:14px;text-align:center;text-transform:uppercase;text-decoration:none}
.hero-btn{left:325px;top:302px;width:156px;height:37px;line-height:37px}
.dots{top:493px;left:553px;display:flex;gap:14px}
.dots span{width:12px;height:12px;border-radius:50%;background:var(--white)}

.section-title{left:0;width:1200px;text-align:center;font-size:32px;color:var(--ink)}
.steps-title{top:580px}
.step-line{top:692px;left:322px;width:556px;height:14px}
.step{width:300px;text-align:center}
.step .num{width:62px;height:62px;border-radius:50%;background:var(--circle);margin:0 auto;font-size:28px;line-height:62px}
.step h3{font-size:31px;margin-top:4px;line-height:44px}
.step p{font-size:11px;line-height:20px;font-weight:600;color:var(--ink);width:275px;margin:6px auto 0}

.who-img{top:918px;left:97px;width:505px;height:368px;background:linear-gradient(135deg,#7a2a22 0%,#a0463a 40%,#d5b58f 60%,#c9a57a 100%)}
.who{top:918px;left:637px;width:424px}
.who h2{font-size:32px;line-height:44px}
.who p{font-size:11.5px;line-height:21px;text-align:justify;margin-top:14px}
.who h3{font-size:20px;margin-top:18px}
.who ul{list-style:none;margin-top:8px}
.who li{font-size:11.5px;line-height:30.7px;display:flex;align-items:center;gap:10px}
.who li::before{content:"";border-left:6px solid var(--ink);border-top:4px solid transparent;border-bottom:4px solid transparent}

.fee-title{top:1350px}
.fee-text{top:1422px;left:240px;width:720px;text-align:center;font-size:14px;line-height:21px}
.phone-badge{top:1474px;left:576px;width:49px;height:49px;border-radius:50%;background:var(--blue);display:flex;align-items:center;justify-content:center}
.fee-number{top:1530px;left:0;width:1200px;text-align:center;font-size:35px}
.fee-btn{top:1590px;left:523px;width:155px;height:36px;line-height:36px}

.faq-band{top:1665px;left:0;width:1200px;height:423px;background:var(--light)}
.faq-title{top:1703px}
.faq-open{top:1788px;left:97px;width:479px;height:234px;background:var(--white);border:1px solid var(--line)}
.faq-head{display:flex;height:50px;background:var(--blue);color:var(--white);font-size:14px;font-weight:600;align-items:center}
.faq-head span{flex:1;padding-left:16px}
.faq-head b{width:54px;height:50px;border-left:1px solid rgba(255,255,255,.6);text-align:center;line-height:48px;font-size:20px}
.faq-open p{padding:14px 16px;font-size:11.5px;line-height:21px;color:var(--muted);text-align:justify}
.faq-item{left:620px;width:479px;height:51px;background:var(--white);border:1px solid var(--line);display:flex;align-items:center;font-size:14px}
.faq-item span{flex:1;padding-left:16px}
.faq-item b{width:53px;height:51px;background:var(--blue);color:var(--white);text-align:center;line-height:51px;font-size:18px;margin-right:-1px}

.footer-nav{top:2120px;left:0;width:1200px;display:flex;justify-content:center;gap:30px;font-family:"Noto Serif",serif;font-size:13px}
.footer-nav a{color:var(--ink);text-decoration:none}
.social{top:2156px;left:502px;display:flex;gap:13px}
.social span{width:38px;height:38px;border-radius:50%;background:var(--social);display:flex;align-items:center;justify-content:center}
.social span::after{content:"";width:7px;height:7px;border-radius:50%;background:var(--ink)}
.social span.on{background:var(--blue)}
.social span.on::after{background:var(--white)}
.copyright{top:2236px;left:0;width:1200px;height:45px;background:var(--dark);color:#c3cad0;font-size:12px;text-align:center;line-height:45px}
.copyright a{color:var(--blue);text-decoration:none}
</style>
</head>
<body>

<div class="abs topbar">
  <div class="abs call">
    <svg width="13" height="13" viewBox="0 0 24 24"><path fill="#333" d="M6.6 10.8a15 15 0 0 0 6.6 6.6l2.2-2.2c.3-.3.7-.4 1-.2 1.1.4 2.3.6 3.6.6.6 0 1 .4 1 1V20c0 .6-.4 1-1 1A17 17 0 0 1 3 4c0-.6.4-1 1-1h3.5c.6 0 1 .4 1 1 0 1.3.2 2.5.6 3.6.1.3 0 .7-.2 1z"/></svg>
    Call Us : 1-800 555 0142
  </div>
</div>

<header class="abs header">
  <div class="abs logo serif">The Velmar Hollow Group</div>
  <nav class="abs nav">
    <a class="active" href="#">Home</a><a href="#">About</a><a href="#">Probate</a><a href="#">Process</a><a href="#">FAQ</a><a href="#">Contact Us</a><a href="#">Blog</a>
  </nav>
</header>

<section>
  <div class="abs hero-scene" role="img" aria-label="City skyline across the bay"></div>
  <div class="abs hero-photo" role="img" aria-label="Smiling older couple sitting together"></div>
  <h1 class="abs hero-title serif">Helping Californians deal with loss with<br>DIGNITY &amp; UNDERSTATING</h1>
  <a class="abs btn hero-btn" href="#">Learn More</a>
  <div class="abs dots"><span></span><span></span><span></span><span></span></div>
</section>

<section>
  <h2 class="abs section-title serif steps-title">Steps in Probate</h2>
  <svg class="abs step-line" viewBox="0 0 556 14">
    <line x1="0" y1="7" x2="242" y2="7" stroke="#bbb" stroke-dasharray="4 3"/>
    <polyline points="235,1 242,7 235,13" fill="none" stroke="#999"/>
    <line x1="312" y1="7" x2="556" y2="7" stroke="#bbb" stroke-dasharray="4 3"/>
    <polyline points="548,1 555,7 548,13" fill="none" stroke="#999"/>
  </svg>
  <div class="abs step" style="left:141px;top:668px"><div class="num serif">01</div><h3 class="serif">Gather</h3><p>Lorem ipsum dolor sit amet, consectetur adipiscing elit, sed do eiusmod tempor incididunt ut labore et dolore magna aliqua. Ut enim ad minim veniam, quis nostrud exercitation ullamco laboris</p></div>
  <div class="abs step" style="left:450px;top:668px"><div class="num serif">02</div><h3 class="serif">Implement</h3><p>Lorem ipsum dolor sit amet, consectetur adipiscing elit, sed do eiusmod tempor incididunt ut labore et dolore magna aliqua. Ut enim ad minim veniam, quis nostrud exercitation ullamco laboris</p></div>
  <div class="abs step" style="left:758px;top:668px"><div class="num serif">03</div><h3 class="serif">Close</h3><p>Lorem ipsum dolor sit amet, consectetur adipiscing elit, sed do eiusmod tempor incididunt ut labore et dolore magna aliqua. Ut enim ad minim veniam, quis nostrud exercitation ullamco laboris</p></div>
</section>

<section>
  <div class="abs who-img" role="img" aria-label="Last will and testament document with pen, pocket watch and keys"></div>
  <div class="abs who">
    <h2 class="serif">Who We Are?</h2>
    <p>Nam libero tempore, cum soluta nobis est eligendi optio cumque nihil impedit quo minus id quod maxime placeat facere possimus, omnis voluptas assumenda est, omnis dolor repellendus.</p>
    <h3 class="serif">What we do?</h3>
    <ul>
      <li>Temporibus autem quibusdam et aut officiis</li>
      <li>Debitis aut rerum necessitatibus saepe</li>
      <li>Eveniet ut et voluptates repudiandae</li>
      <li>Temporibus autem quibusdam et aut officiis</li>
      <li>Debitis aut rerum necessitatibus saepe</li>
      <li>Eveniet ut et voluptates repudiandae</li>
    </ul>
  </div>
</section>

<section>
  <h2 class="abs section-title serif fee-title">Flat-Fee Price &amp; Savings</h2>
  <p class="abs fee-text">Lorem ipsum dolor sit amet, consectetur adipiscing elit, sed do eiusmod tempor incididunt ut labore et dolore magna aliqua. Ut enim ad minim veniam, quis nostrud exercitation ullamco laboris</p>
  <div class="abs phone-badge">
    <svg width="22" height="22" viewBox="0 0 24 24"><path fill="#fff" d="M6.6 10.8a15 15 0 0 0 6.6 6.6l2.2-2.2c.3-.3.7-.4 1-.2 1.1.4 2.3.6 3.6.6.6 0 1 .4 1 1V20c0 .6-.4 1-1 1A17 17 0 0 1 3 4c0-.6.4-1 1-1h3.5c.6 0 1 .4 1 1 0 1.3.2 2.5.6 3.6.1.3 0 .7-.2 1z"/></svg>
  </div>
  <div class="abs fee-number serif">1-800 555 0142</div>
  <a class="abs btn fee-btn" href="tel:18005550142">Contact Us</a>
</section>

<section>
  <div class="abs faq-band"></div>
  <h2 class="abs section-title serif faq-title">FAQs</h2>
  <div class="abs faq-open">
    <div class="faq-head"><span>What is Lorem Ipsum?</span><b>−</b></div>
    <p>Nam libero tempore, cum soluta nobis est eligendi optio cumque nihil impedit quo minus id quod maxime placeat facere possimus, omnis voluptas assumenda est, omnis dolor repellendus. Temporibus autem quibusdam et aut officiis debitis aut rerum necessitatibus saepe eveniet ut et voluptates repudiandae sint et molestiae non recusandae. Itaque earum rerum hic tenetur</p>
  </div>
  <div class="abs faq-item" style="top:1788px"><span>What is Lorem Ipsum?</span><b>+</b></div>
  <div class="abs faq-item" style="top:1850px"><span>What is Lorem Ipsum?</span><b>+</b></div>
  <div class="abs faq-item" style="top:1912px"><span>What is Lorem Ipsum?</span><b>+</b></div>
  <div class="abs faq-item" style="top:1975px"><span>What is Lorem Ipsum?</span><b>+</b></div>
</section>

<footer>
  <nav class="abs footer-nav"><a href="#">Home</a><a href="#">About</a><a href="#">Probate</a><a href="#">Process</a><a href="#">FAQ</a><a href="#">Contact Us</a><a href="#">Blog</a></nav>
  <div class="abs social"><span aria-label="Social link"></span><span class="on" aria-label="Social link"></span><span aria-label="Social link"></span><span aria-label="Social link"></span></div>
  <div class="abs copyright">Copyright © 2017 <a href="#">www.velmarhollow.com</a> &nbsp;| All Rights Reserved</div>
</footer>

</body>
</html>
```